Business Card Design for Training Business

Clear Path Coaching is a new business that delivers training and other services with a focus on topics related to mental health and wellbeing, for example, Wellmind Response Course, Resilience etc. We have a strong focus on evidence-based psychology and neuroscience. I have a logo which I will upload with the brief, so please consider colours that work well with the logo.
Target Market(s)
Adults, workplaces (particularly government and not-for-profits)
Industry/Entity Type
Business
Contact Information for Business Card
Head Strong TrainingSamantha SellwoodDirector0438 770 850sam@headstrongtraining.com.auwww.headstrongtraining.com.au

```html
<!DOCTYPE html>
<html lang="en">
<head>
<meta charset="utf-8">
<title>Clear Path Coaching – Business Card</title>
<link rel="stylesheet" href="https://fonts.googleapis.com/css2?family=Raleway:wght@300;400;500&display=swap">
<style>
  :root {
    --page-bg: #d9d6d1;
    --card-frost-top: #f2f4f3;
    --card-frost-bottom: #dfe6e6;
    --teal-deep: #1b8587;
    --teal-light: #5cbcbc;
    --arc-line: #3a3434;
    --brand-text: #4a4646;
    --name-teal: #259597;
    --role-text: #2d2a2a;
    --contact-text: #eef7f7;
  }
  html, body {
    margin: 0;
    width: 1200px;
    height: 969px;
    overflow: hidden;
    background: var(--page-bg);
    font-family: "Raleway", Arial, sans-serif;
  }
  .card {
    position: absolute;
    left: 100px;
    top: 201px;
    width: 1000px;
    height: 567px;
    border-radius: 30px;
    overflow: hidden;
    background: linear-gradient(180deg, var(--card-frost-top), var(--card-frost-bottom));
    box-shadow: 0 10px 30px rgba(0,0,0,0.18);
  }
  .card-shapes {
    position: absolute;
    inset: 0;
  }
  .brand-mark {
    position: absolute;
    left: 50%;
    top: 24px;
    width: 140px;
    height: 140px;
    margin-left: -70px;
    box-sizing: border-box;
    border: 4px solid var(--name-teal);
    border-radius: 50%;
  }
  .brand-name {
    position: absolute;
    left: 0;
    right: 0;
    top: 196px;
    margin: 0;
    text-align: center;
    font-weight: 300;
    font-size: 46px;
    letter-spacing: 5px;
    color: var(--brand-text);
  }
  .person-name {
    position: absolute;
    left: 0;
    right: 0;
    top: 318px;
    margin: 0;
    text-align: center;
    font-weight: 400;
    font-size: 37px;
    color: var(--name-teal);
  }
  .person-role {
    position: absolute;
    left: 0;
    right: 0;
    top: 366px;
    margin: 0;
    text-align: center;
    font-weight: 400;
    font-size: 27px;
    color: var(--role-text);
  }
  .contact-row {
    position: absolute;
    left: 0;
    right: 0;
    display: flex;
    justify-content: center;
    gap: 44px;
    font-weight: 300;
    font-size: 24px;
    color: var(--contact-text);
  }
  .contact-row.primary { top: 462px; }
  .contact-row.web { top: 502px; }
  .contact-item {
    display: flex;
    align-items: center;
    gap: 12px;
  }
  .contact-icon {
    width: 24px;
    height: 24px;
    fill: var(--contact-text);
  }
</style>
</head>
<body>
  <div class="card">
    <svg class="card-shapes" viewBox="0 0 1000 567" width="1000" height="567" aria-hidden="true">
      <defs>
        <linearGradient id="tealBand" x1="0" y1="0" x2="1" y2="1">
          <stop offset="0" stop-color="var(--teal-deep)"/>
          <stop offset="0.55" stop-color="var(--teal-light)"/>
          <stop offset="1" stop-color="var(--teal-deep)"/>
        </linearGradient>
      </defs>
      <path d="M0,150 C250,505 750,505 1000,195 L1000,567 L0,567 Z" fill="url(#tealBand)"/>
      <path d="M0,176 C250,530 750,530 1000,218" fill="none" stroke="var(--arc-line)" stroke-width="8"/>
    </svg>

    <div class="brand-mark"></div>
    <p class="brand-name">CLEAR PATH COACHING</p>

    <p class="person-name">Rebecca Tanfield</p>
    <p class="person-role">Director</p>

    <div class="contact-row primary">
      <span class="contact-item">
        <svg class="contact-icon" viewBox="0 0 24 24" aria-hidden="true"><path d="M6.6 10.8a15.1 15.1 0 0 0 6.6 6.6l2.2-2.2a1 1 0 0 1 1-.25 11.4 11.4 0 0 0 3.6.57 1 1 0 0 1 1 1V20a1 1 0 0 1-1 1A17 17 0 0 1 3 4a1 1 0 0 1 1-1h3.5a1 1 0 0 1 1 1c0 1.25.2 2.45.57 3.57a1 1 0 0 1-.25 1z"/></svg>
        0491 362 517
      </span>
      <span class="contact-item">
        <svg class="contact-icon" viewBox="0 0 24 24" aria-hidden="true"><path d="M2 5h20v14H2z M4 7v.4l8 5 8-5V7z" fill-rule="evenodd"/></svg>
        bec@clearpathcoaching.example.au
      </span>
    </div>
    <div class="contact-row web">
      <span class="contact-item">
        <svg class="contact-icon" viewBox="0 0 24 24" aria-hidden="true"><path d="M12 2a10 10 0 1 0 0 20 10 10 0 0 0 0-20zm0 2c.9 0 2.2 2 2.7 5H9.3C9.8 6 11.1 4 12 4zM4.3 11h3a16 16 0 0 0 0 2h-3a8 8 0 0 1 0-2zm5 0h5.4a14 14 0 0 1 0 2H9.3a14 14 0 0 1 0-2zm7.4 0h3a8 8 0 0 1 0 2h-3a16 16 0 0 0 0-2zM12 20c-.9 0-2.2-2-2.7-5h5.4c-.5 3-1.8 5-2.7 5z"/></svg>
        www.clearpathcoaching.example.au
      </span>
    </div>
  </div>
</body>
</html>
```